Restyle corporate identity (+ logo) for a road construction company

We need a new logo and stationary design for our company VARNOK path. VARNOK path® increases the road base strength, while reducing major costs and time of road construction. Attached some examples of the current design.

Our wishes for the new logo:
- Business look
- Style sheet
- Modern

More information: www.varnokpath.example
Updates

Target Market(s)

Government

Industry/Entity Type

Construction

Requirements
Must have
• Logo (with road sign) + text

```html
<!DOCTYPE html>
<html lang="en">
<head>
<meta charset="utf-8">
<title>VARNOK path – Stationery</title>
<link href="https://fonts.googleapis.com/css2?family=Open+Sans:wght@400;600;700&display=swap" rel="stylesheet">
<style>
:root{
  --green:#9dc43c;
  --gray:#8a8b8d;
  --dark:#404042;
  --ink:#555658;
  --paper:#ffffff;
  --paper-soft:#f4f4f4;
  --road:#d9d9da;
  --bg:#ececec;
}
*{box-sizing:border-box;margin:0;padding:0}
html,body{width:1200px;height:867px;overflow:hidden}
body{background:var(--bg);font-family:"Open Sans",Arial,sans-serif;color:var(--ink);position:relative}
.sheet{position:absolute;background:var(--paper);box-shadow:0 3px 10px rgba(0,0,0,.18);overflow:hidden}
.brand{display:flex;align-items:center;gap:10px}
.brand-mark{background:var(--green);border-radius:3px;flex:none}
.brand-name{font-weight:700;color:var(--gray);white-space:nowrap;letter-spacing:.5px}
.road-art{position:absolute;background:linear-gradient(135deg,var(--road),#ececec);}
.contact{font-size:8px;line-height:1.45}
.contact b{font-weight:700}
.contact .lbl{color:var(--green);font-weight:600}

/* envelope */
.envelope{left:40px;top:50px;width:520px;height:230px;background:var(--paper-soft)}
.envelope .tab{position:absolute;right:0;top:0;width:300px;height:20px;background:var(--green);border-bottom-left-radius:14px}
.envelope .brand{position:absolute;left:22px;top:40px}
.envelope .brand-mark{width:40px;height:40px}
.envelope .brand-name{font-size:22px}
.envelope .road-art{right:0;top:90px;width:96px;height:120px;border-top-left-radius:80px}
.envelope .contact{position:absolute;left:22px;top:155px}
.envelope .url{position:absolute;right:14px;bottom:18px;font-size:8px;font-weight:600}
.envelope .band-g{position:absolute;left:0;bottom:0;width:330px;height:18px;background:var(--green);border-top-right-radius:14px}
.envelope .band-d{position:absolute;right:0;bottom:0;width:200px;height:14px;background:var(--gray)}

/* business cards */
.card{top:330px;width:250px;height:144px}
.card-front{left:40px;background:var(--dark)}
.card-front .brand{position:absolute;left:36px;top:50px}
.card-front .brand-mark{width:30px;height:30px}
.card-front .brand-name{font-size:20px;color:#fff}
.card-front .rule{position:absolute;left:20px;right:20px;bottom:26px;height:1px;background:var(--green)}
.card-front .url{position:absolute;right:20px;bottom:10px;font-size:7px;color:var(--green)}
.card-back{left:320px}
.card-back .brand{position:absolute;left:16px;top:12px}
.card-back .brand-mark{width:22px;height:22px}
.card-back .brand-name{font-size:15px}
.card-back .person{position:absolute;left:18px;top:50px;font-size:8px;font-weight:700}
.card-back .person span{display:block;color:var(--green);font-weight:600;font-size:7px}
.card-back .contact{position:absolute;left:110px;top:50px;font-size:7px}
.card-back .rule{position:absolute;left:18px;right:18px;top:44px;height:1px;background:var(--green)}
.card-back .road-art{right:0;bottom:14px;width:70px;height:50px;border-top-left-radius:40px}
.card-back .foot-g{position:absolute;left:0;bottom:0;width:150px;height:14px;background:var(--green);border-top-right-radius:10px;color:#fff;font-size:6px;line-height:14px;padding-left:10px}
.card-back .foot-d{position:absolute;right:0;bottom:0;width:110px;height:10px;background:var(--dark)}

/* letterhead */
.letterhead{left:600px;top:36px;width:380px;height:537px}
.letterhead .top-d{position:absolute;left:0;top:0;width:170px;height:8px;background:var(--gray)}
.letterhead .top-g{position:absolute;right:0;top:0;width:215px;height:14px;background:var(--green);border-bottom-left-radius:10px}
.letterhead .brand{position:absolute;left:26px;top:30px}
.letterhead .brand-mark{width:26px;height:26px}
.letterhead .brand-name{font-size:17px}
.letterhead .rule{position:absolute;left:26px;right:26px;top:68px;height:1px;background:var(--green)}
.letterhead .contact{position:absolute;right:26px;top:26px;text-align:right;font-size:7px}
.letterhead .road-art{left:130px;bottom:14px;width:250px;height:150px;border-top-left-radius:120px}
.letterhead .bot-g{position:absolute;left:0;bottom:0;width:210px;height:14px;background:var(--green);border-top-right-radius:10px}
.letterhead .bot-d{position:absolute;right:0;bottom:0;width:175px;height:8px;background:var(--gray)}

/* lockups */
.lockup-small{position:absolute;left:40px;top:770px}
.lockup-small .brand-mark{width:56px;height:56px}
.lockup-small .divider{width:1px;height:64px;background:var(--gray);margin:0 6px}
.lockup-small .brand-name{font-size:30px}
.lockup-large{position:absolute;left:800px;top:630px;flex-direction:column;align-items:center;gap:16px}
.lockup-large .brand-mark{width:130px;height:130px;border-radius:8px}
.lockup-large .brand-name{font-size:48px}
</style>
</head>
<body>

<section class="sheet envelope" aria-label="Envelope">
  <div class="tab"></div>
  <div class="brand"><div class="brand-mark"></div><div class="brand-name">VARNOK path</div></div>
  <div class="road-art" role="img" aria-label="Soft grey winding road decoration"></div>
  <div class="contact">
    <b>Address Line 1, Address Line2,<br>Address Line 3</b><br>
    <span class="lbl">Email</span> - yourmail@varnokpath.example<br>
    <span class="lbl">Tel.</span> - +123 456 780<br>
    <span class="lbl">Fax.</span> - +123 456 789
  </div>
  <div class="url">www.varnokpath.example</div>
  <div class="band-d"></div>
  <div class="band-g"></div>
</section>

<section class="sheet card card-front" aria-label="Business card front">
  <div class="brand"><div class="brand-mark"></div><div class="brand-name">VARNOK path</div></div>
  <div class="rule"></div>
  <div class="url">www.varnokpath.example</div>
</section>

<section class="sheet card card-back" aria-label="Business card back">
  <div class="brand"><div class="brand-mark"></div><div class="brand-name">VARNOK path</div></div>
  <div class="rule"></div>
  <div class="person">YOUR NAME<span>Position</span></div>
  <div class="contact">
    +123 456 780<br>+123 456 789<br>yourmail@varnokpath.example<br>www.varnokpath.example
  </div>
  <div class="road-art" role="img" aria-label="Soft grey winding road decoration"></div>
  <div class="foot-d"></div>
  <div class="foot-g">Address Line 1, Address Line 2, Address Line 3</div>
</section>

<section class="sheet letterhead" aria-label="Letterhead">
  <div class="top-d"></div>
  <div class="top-g"></div>
  <div class="brand"><div class="brand-mark"></div><div class="brand-name">VARNOK path</div></div>
  <div class="contact">
    <b>Address Line 1, Address Line2,<br>Address Line 3</b><br>
    +123 456 780<br>+123 456 789<br>yourmail@varnokpath.example<br>www.varnokpath.example
  </div>
  <div class="rule"></div>
  <div class="road-art" role="img" aria-label="Large soft grey winding road decoration"></div>
  <div class="bot-d"></div>
  <div class="bot-g"></div>
</section>

<div class="brand lockup-small" aria-label="Horizontal logo lockup">
  <div class="brand-mark"></div>
  <div class="divider"></div>
  <div class="brand-name">VARNOK path</div>
</div>

<div class="brand lockup-large" aria-label="Stacked logo lockup">
  <div class="brand-mark"></div>
  <div class="brand-name">VARNOK path</div>
</div>

</body>
</html>
```